Health Care Company with Logo Needs Business Cards designed

We are a luxury behavioral health company looking for business cards design we already have a logo and are looking for someone to design a sophisticated luxurious looking business card. Please note that Card design should be captivating just like the logo and also encompass the logo color

Industry/Entity Type

Healthcare

Contact Information for Business Card

Logo,company name, tagline, my name and title, contact details, and physical address

```html
<!DOCTYPE html>
<html lang="en">
<head>
<meta charset="utf-8">
<title>Corvin Behavioral Health – Business Cards</title>
<link href="https://fonts.googleapis.com/css2?family=Roboto+Condensed:wght@700&family=Roboto:ital,wght@0,400;0,500;1,400&display=swap" rel="stylesheet">
<style>
  :root {
    --page: #2a2a2b;
    --card: #222224;
    --purple: #74387f;
    --purple-deep: #5e2d68;
    --purple-text: #8a3a8e;
    --blue: #1a94d4;
    --white: #f2f2f2;
  }
  html, body {
    margin: 0;
    padding: 0;
    width: 1200px;
    height: 1138px;
    overflow: hidden;
    background: var(--page);
  }
  .card {
    position: absolute;
    left: 277px;
    width: 620px;
    height: 374px;
    border-radius: 14px;
    background: var(--card);
    overflow: hidden;
  }
  .card--front { top: 186px; }
  .card--back { top: 608px; }

  .front-brand {
    position: absolute;
    left: 40px;
    top: 168px;
  }
  .front-brand__name {
    font: 700 25px/1 "Roboto Condensed", sans-serif;
    color: var(--purple-text);
    margin: 0;
  }
  .front-brand__tagline {
    font: 500 7.5px/1 "Roboto", sans-serif;
    letter-spacing: 1.7px;
    color: var(--white);
    margin: 6px 0 0;
  }

  .back-brand {
    position: absolute;
    left: 40px;
    top: 50px;
    display: flex;
    align-items: center;
    gap: 18px;
  }
  .back-brand__square {
    width: 68px;
    height: 68px;
    background: var(--purple);
  }
  .back-brand__name {
    font: 700 40px/1 "Roboto Condensed", sans-serif;
    color: var(--purple);
    margin: 0;
  }
  .back-brand__tagline {
    font: 700 12.5px/1 "Roboto Condensed", sans-serif;
    letter-spacing: 3.4px;
    color: var(--blue);
    margin: 6px 0 0;
  }

  .person {
    position: absolute;
    left: 40px;
    top: 192px;
  }
  .person__name {
    font: 500 22px/1 "Roboto", sans-serif;
    color: var(--purple-text);
    margin: 0 0 0 4px;
  }
  .person__title {
    font: italic 400 16px/1 "Roboto", sans-serif;
    color: var(--white);
    margin: 9px 0 0;
  }

  .accent-area {
    position: absolute;
    left: 0;
    right: 0;
    bottom: 0;
    height: 132px;
    background: linear-gradient(100deg, var(--card) 0%, var(--purple-deep) 38%, var(--purple) 100%);
  }

  .contact {
    position: absolute;
    right: 36px;
    top: 258px;
    text-align: right;
    font: 400 15px/22px "Roboto", sans-serif;
    color: var(--white);
  }
  .contact__row {
    display: flex;
    justify-content: flex-end;
    align-items: center;
    gap: 12px;
    margin-right: 7px;
  }
  .contact__row svg { width: 14px; height: 14px; }
  .contact__address {
    font-size: 16px;
    margin-top: 5px;
  }
</style>
</head>
<body>

<section class="card card--front">
  <div class="front-brand">
    <p class="front-brand__name">Corvin Behavioral Health</p>
    <p class="front-brand__tagline">DEDICATED TO HOPE, HEALING AND RECOVERY</p>
  </div>
</section>

<section class="card card--back">
  <div class="accent-area" role="img" aria-label="Decorative band in purple, blue and orange tones"></div>

  <div class="back-brand">
    <div class="back-brand__square"></div>
    <div>
      <p class="back-brand__name">Corvin Behavioral Health</p>
      <p class="back-brand__tagline">DEDICATED TO HOPE, HEALING AND RECOVERY</p>
    </div>
  </div>

  <div class="person">
    <p class="person__name">MARTIN CORVIN</p>
    <p class="person__title">Managing Director</p>
  </div>

  <div class="contact">
    <div class="contact__row">000-222-0000
      <svg viewBox="0 0 14 14"><path fill="#f2f2f2" d="M1 5 C1 2 13 2 13 5 L10 6 L9 4 L5 4 L4 6 Z M3 7 L11 7 L12 12 L2 12 Z"/></svg>
    </div>
    <div class="contact__row">corvinbehavioral.com
      <svg viewBox="0 0 14 14"><rect x="1" y="3" width="12" height="9" fill="#f2f2f2"/><path d="M1 3 L7 8 L13 3 M1 12 L5.5 7 M13 12 L8.5 7" stroke="#74387f" stroke-width="1.2" fill="none"/></svg>
    </div>
    <div class="contact__row">hello@corvinbehavioral.com
      <svg viewBox="0 0 14 14"><circle cx="7" cy="7" r="6" fill="none" stroke="#f2f2f2" stroke-width="1.3"/><ellipse cx="7" cy="7" rx="2.6" ry="6" fill="none" stroke="#f2f2f2" stroke-width="1.1"/><path d="M1 7 H13 M2 4 H12 M2 10 H12" stroke="#f2f2f2" stroke-width="1"/></svg>
    </div>
    <div class="contact__address">45, Elm Row, Any Town, US 123456</div>
  </div>
</section>

</body>
</html>
```